Oriel Photography Business Card

I need a business card designed for a photography business based in Perth, Western Australia called Oriel Photography.

We specialise in wedding, event photography and portrait photography.

The business card must borrow the style of the attached logo.

The hex codes for the colours in the logo are:
#ED1D85 - Pink
#89C23E - Green
#37282F - Black

The name on the card will be:
Name: Tobrian
Phone: 0417395268
Website: www.orielphotography.example.com.au
Facebook: orielphotography

I am open and happy to accept creative concepts.

I’d like some space at the back for writing notes and appointment details.

```html
<!DOCTYPE html>
<html lang="en">
<head>
<meta charset="utf-8">
<title>Oriel Photography – Business Card</title>
<link rel="stylesheet" href="https://fonts.googleapis.com/css2?family=Raleway:wght@400&family=Open+Sans:wght@400;600;700&display=swap">
<style>
  :root {
    --pink: #ED1D85;
    --pink-faint: #FCE3EF;
    --green: #89C23E;
    --green-card: #A3C93F;
    --ink: #37282F;
    --paper: #FFFFFF;
    --backdrop: #ECEAE6;
    --rule: #9A9A9A;
    --social-blue: #3B5998;
  }
  * { margin: 0; padding: 0; box-sizing: border-box; }
  html, body { width: 1200px; height: 720px; overflow: hidden; }
  body {
    background: var(--backdrop);
    font-family: "Open Sans", Arial, sans-serif;
    color: var(--ink);
    position: relative;
  }
  .card {
    position: absolute;
    top: 205px;
    width: 540px;
    height: 310px;
    overflow: hidden;
    box-shadow: 0 6px 18px rgba(0,0,0,0.12);
  }
  .card--front { left: 40px; background: var(--paper); }
  .card--back  { left: 620px; background: var(--green-card); }

  .brand-mark {
    position: absolute;
    border-radius: 50%;
  }
  .card--front .brand-mark { left: 212px; top: 26px; width: 66px; height: 66px; background: var(--pink); }
  .card--back  .brand-mark { left: 242px; top: 26px; width: 56px; height: 56px; background: var(--ink); }

  .brand-name {
    position: absolute;
    left: 0; right: 0;
    text-align: center;
    font-family: "Raleway", Arial, sans-serif;
    font-weight: 400;
    text-transform: uppercase;
    color: var(--ink);
    letter-spacing: 0.62em;
    padding-left: 0.62em;
    white-space: nowrap;
  }
  .card--front .brand-name { top: 112px; font-size: 14px; }
  .card--back  .brand-name { top: 100px; font-size: 13px; }

  .contact-list {
    position: absolute;
    left: 26px;
    top: 200px;
    list-style: none;
    font-size: 14px;
  }
  .contact-list li {
    display: flex;
    align-items: center;
    gap: 8px;
    height: 24px;
  }
  .contact-icon { width: 14px; height: 14px; flex: none; }

  .holder-badge {
    position: absolute;
    left: 396px;
    top: 152px;
    width: 124px;
    height: 124px;
    border-radius: 50%;
    background: var(--pink-faint);
    display: flex;
    align-items: center;
    justify-content: center;
  }
  .holder-name {
    font-weight: 700;
    font-size: 20px;
    color: var(--pink);
    text-transform: uppercase;
    letter-spacing: 0.02em;
  }

  .notes-panel {
    position: absolute;
    left: 0;
    right: 18px;
    top: 134px;
    height: 132px;
    background: var(--paper);
  }
  .notes-lines { position: absolute; left: 16px; right: 18px; top: 0; height: 100%; }
  .notes-lines span {
    position: absolute;
    left: 0; right: 0;
    border-top: 1px dotted var(--rule);
  }
  .notes-lines .after-label { left: 60px; }
  .notes-label {
    position: absolute;
    left: 16px;
    top: 50px;
    font-size: 16px;
    font-weight: 600;
    line-height: 20px;
    color: #000;
  }

  .back-website {
    position: absolute;
    left: 0; right: 0;
    top: 276px;
    text-align: center;
    font-size: 15px;
    letter-spacing: 0.08em;
    color: var(--ink);
  }
</style>
</head>
<body>

<section class="card card--front" aria-label="Business card front">
  <div class="brand-mark" aria-hidden="true"></div>
  <div class="brand-name">Oriel Photography</div>

  <div class="holder-badge">
    <span class="holder-name">Tobrian</span>
  </div>

  <ul class="contact-list">
    <li>
      <svg class="contact-icon" viewBox="0 0 14 14" aria-hidden="true">
        <circle cx="7" cy="7" r="7" fill="var(--green)"/>
        <path d="M4.5 3.5l1.5 0 .7 1.8-.9.7a5 5 0 0 0 2.2 2.2l.7-.9 1.8.7 0 1.5c-3.5.3-6.3-2.5-6-6z" fill="#fff"/>
      </svg>
      0417395268
    </li>
    <li>
      <svg class="contact-icon" viewBox="0 0 14 14" aria-hidden="true">
        <circle cx="7" cy="7" r="7" fill="var(--social-blue)"/>
      </svg>
      orielphotography
    </li>
    <li>
      <svg class="contact-icon" viewBox="0 0 14 14" aria-hidden="true">
        <circle cx="7" cy="7" r="7" fill="var(--green)"/>
        <circle cx="7" cy="7" r="4" fill="none" stroke="#fff" stroke-width="1"/>
        <path d="M3 7h8M7 3c-1.6 2.4-1.6 5.6 0 8M7 3c1.6 2.4 1.6 5.6 0 8" fill="none" stroke="#fff" stroke-width="0.8"/>
      </svg>
      www.orielphotography.example.com.au
    </li>
  </ul>
</section>

<section class="card card--back" aria-label="Business card back">
  <div class="brand-mark" aria-hidden="true"></div>
  <div class="brand-name">Oriel Photography</div>

  <div class="notes-panel">
    <div class="notes-lines" aria-hidden="true">
      <span style="top:20px"></span>
      <span style="top:44px"></span>
      <span style="top:68px" class="after-label"></span>
      <span style="top:92px"></span>
      <span style="top:116px"></span>
    </div>
    <p class="notes-label">notes:</p>
  </div>

  <div class="back-website">www.orielphotography.example.com.au</div>
</section>

</body>
</html>
```